Brightbay Orthodontics business card design

Need a business card design that reflects our re-branding (orthodontic office - braces) and a new partnership with a pediatric dental office. We would like to include "for adults and children" on the card as well so adults know they are welcome to get their braces here as well. Office design is modern and would like business card to reflect a modern type look. Here's the text we would like to be included on the card:

Darren Wolcott, DDS, MSD
5214 West Linden Avenue, Suite 204
Mansfield, TX 76991
555-418-2637
www.brightbayortho.example
info@brightbayortho.example

Can we add the following to the existing designs? Darren Wolcott, DDS, MSD 5214 West Linden Avenue, Suite 204 Mansfield, TX 76991 555-418-2637

Does anyone have any more vertical designs available? Thanks!

Dental

```html
<!DOCTYPE html>
<html lang="en">
<head>
<meta charset="utf-8">
<title>Brightbay Orthodontics – Business Card</title>
<link rel="stylesheet" href="https://fonts.googleapis.com/css2?family=Open+Sans:wght@400;600;700&display=swap">
<style>
  :root {
    --backdrop: #e4e4e2;
    --card: #ffffff;
    --ink: #2a2a2a;
    --muted: #555555;
    --name-blue: #1f6fb5;
    --icon-green: #4aa04a;
    --band-yellow: #f4e300;
    --band-blue: #1c73b8;
    --band-magenta: #d6197f;
    --band-green: #6aa533;
    --band-orange: #d9790f;
  }
  * { box-sizing: border-box; margin: 0; padding: 0; }
  html, body { width: 1200px; height: 871px; overflow: hidden; }
  body {
    background: var(--backdrop);
    font-family: "Open Sans", Arial, sans-serif;
    color: var(--ink);
    position: relative;
  }
  .card {
    position: absolute;
    width: 640px;
    height: 366px;
    background: var(--card);
    box-shadow: 0 8px 24px rgba(0,0,0,.18);
    overflow: hidden;
  }
  .card--front { left: 100px; top: 64px; background: linear-gradient(135deg, #f7f7f7, #e9e9e9); }
  .card--back  { left: 460px; top: 448px; }

  .color-band {
    position: absolute; left: 0; right: 0; bottom: 0; height: 16px;
    display: flex;
  }
  .color-band span { flex: 1; }
  .color-band .yellow  { background: var(--band-yellow); }
  .color-band .blue    { background: var(--band-blue); }
  .color-band .magenta { background: var(--band-magenta); }
  .color-band .green   { background: var(--band-green); }
  .color-band .orange  { background: var(--band-orange); }

  .brand {
    position: absolute;
    display: flex; align-items: center; gap: 16px;
  }
  .brand__dot { border-radius: 50%; background: var(--band-blue); flex: none; }
  .brand__text { display: flex; flex-direction: column; }
  .brand__name { font-weight: 700; color: var(--ink); line-height: 1.02; }
  .brand__tagline { font-weight: 400; color: var(--muted); letter-spacing: .4px; margin-top: 8px; }

  .card--front .brand { left: 118px; top: 104px; }
  .card--front .brand__dot { width: 58px; height: 58px; }
  .card--front .brand__name { font-size: 50px; }
  .card--front .brand__tagline { font-size: 17px; }

  .card--back .brand { left: 40px; top: 104px; gap: 12px; }
  .card--back .brand__dot { width: 38px; height: 38px; }
  .card--back .brand__name { font-size: 30px; }
  .card--back .brand__tagline { font-size: 12px; margin-top: 6px; }

  .contact {
    position: absolute; left: 352px; top: 92px; width: 270px;
    font-size: 13px; color: var(--ink);
  }
  .contact__name { font-size: 19px; font-weight: 700; color: var(--name-blue); letter-spacing: .5px; }
  .contact__title { font-size: 11px; font-weight: 600; color: var(--muted); margin-bottom: 18px; }
  .contact__address { line-height: 1.45; margin-bottom: 14px; }
  .contact__list { list-style: none; }
  .contact__list li { display: flex; align-items: center; gap: 10px; line-height: 1.9; }
  .contact__list svg { width: 13px; height: 13px; flex: none; }
</style>
</head>
<body>

<section class="card card--front" aria-label="Card front">
  <div class="brand">
    <span class="brand__dot"></span>
    <div class="brand__text">
      <span class="brand__name">Brightbay<br>Orthodontics</span>
      <span class="brand__tagline">for adults and children</span>
    </div>
  </div>
  <div class="color-band">
    <span class="yellow"></span><span class="blue"></span><span class="magenta"></span><span class="green"></span><span class="orange"></span>
  </div>
</section>

<section class="card card--back" aria-label="Card back">
  <div class="brand">
    <span class="brand__dot"></span>
    <div class="brand__text">
      <span class="brand__name">Brightbay<br>Orthodontics</span>
      <span class="brand__tagline">for adults and children</span>
    </div>
  </div>

  <div class="contact">
    <p class="contact__name">Darren Wolcott</p>
    <p class="contact__title">DDS, MSD</p>
    <p class="contact__address">5214 West Linden Avenue, Suite 204<br>Mansfield, TX 76991</p>
    <ul class="contact__list">
      <li>
        <svg viewBox="0 0 16 16" aria-hidden="true"><path fill="var(--icon-green)" d="M3 1.5l3 .5 1 3-2 1.5a9 9 0 0 0 4.5 4.5L11 9l3 1 .5 3-2 1.5C7 14.5 1.5 9 1.5 3.5z"/></svg>
        <span>555-418-2637</span>
      </li>
      <li>
        <svg viewBox="0 0 16 16" aria-hidden="true"><rect x="1" y="3" width="14" height="10" rx="1" fill="var(--icon-green)"/><path d="M1.5 3.5 8 9l6.5-5.5" stroke="#fff" stroke-width="1.4" fill="none"/></svg>
        <span>info@brightbayortho.example</span>
      </li>
      <li>
        <svg viewBox="0 0 16 16" aria-hidden="true"><circle cx="8" cy="8" r="6.5" fill="none" stroke="var(--icon-green)" stroke-width="1.6"/><ellipse cx="8" cy="8" rx="2.8" ry="6.5" fill="none" stroke="var(--icon-green)" stroke-width="1.3"/><path d="M1.5 8h13" stroke="var(--icon-green)" stroke-width="1.3"/></svg>
        <span>www.brightbayortho.example</span>
      </li>
    </ul>
  </div>

  <div class="color-band">
    <span class="yellow"></span><span class="blue"></span><span class="magenta"></span><span class="green"></span><span class="orange"></span>
  </div>
</section>

</body>
</html>
```